Banner Ad for Weight Loss Product Site

We need a banner ad design for a new company selling a weight loss online programme (Ebook). The product is called "Your FitRoute" and is suitable for people that want to lose weight fast and without doing sports, regardless of age. We would like to see designs that are eye-catching and at its best animated like in the example files. The final design should exhibit a professional look that encourages the customers to buy our product. The text should be "Persönlicher Diätplan zum Abnehmen?" as a title and "Jetzt informieren" for the button field. Thank you!

Industry/Entity Type

Weight

```html
<!DOCTYPE html>
<html lang="de">
<head>
<meta charset="utf-8">
<title>Your FitRoute – Banner Set</title>
<link rel="stylesheet" href="https://fonts.googleapis.com/css2?family=Roboto:wght@500;700;900&family=Roboto+Condensed:wght@700&display=swap">
<style>
  :root{
    --sheet:#efefef;
    --sheet-text:#6b6b6b;
    --green:#5aa50e;
    --green-dark:#3f7d06;
    --green-light:#9ed11f;
    --gold:#f4c21a;
    --head-green:#4c9a0c;
    --orange-top:#ffbf1f;
    --orange-bot:#f27a00;
    --btn-text:#3a2a00;
    --panel-top:#ffffff;
    --panel-bot:#e6e6e6;
    --logo-bg:#4d7d12;
    --logo-ring:#e8c13a;
  }
  *{box-sizing:border-box;margin:0;padding:0}
  html,body{width:1200px;height:841px;overflow:hidden;background:var(--sheet)}
  .sheet{position:relative;width:1200px;height:841px;background:var(--sheet);font-family:"Roboto",Arial,sans-serif}
  .sheet-note{position:absolute;left:0;width:100%;text-align:center;font-family:"Roboto Condensed","Roboto",sans-serif;font-weight:700;color:var(--sheet-text);text-transform:uppercase;letter-spacing:1px;font-size:35px;line-height:43px}
  .sheet-note--top{top:36px}
  .sheet-note--bottom{top:708px}

  .banner{position:absolute;overflow:hidden;background:linear-gradient(180deg,var(--panel-top),var(--panel-bot));box-shadow:0 1px 3px rgba(0,0,0,.15)}
  .wave{position:absolute;left:0;width:100%}
  .wave--top{top:0}
  .wave--bottom{bottom:0}

  .logo{position:absolute;border-radius:50%;background:radial-gradient(circle at 40% 35%,#6a9a22,var(--logo-bg));border:3px solid var(--logo-ring);display:flex;align-items:center;justify-content:center;text-align:center;color:#ffffff;font-weight:700;line-height:1.05}

  .headline{position:absolute;color:var(--head-green);font-weight:700;line-height:1.18}

  .photo{position:absolute;border-radius:40% 40% 8% 8%;background:linear-gradient(180deg,#6b4a33 0%,#c99a7c 30%,#2b2b2b 55%,#d4a488 70%,#2a2a2a 100%)}
  .product{position:absolute;border-radius:4px;background:linear-gradient(135deg,#f7f9f2,#cfdcc0 60%,#9fb88a)}

  .cta{position:absolute;display:flex;align-items:center;justify-content:center;gap:6px;border-radius:999px;background:linear-gradient(180deg,var(--orange-top),var(--orange-bot));color:var(--btn-text);font-weight:900;text-transform:uppercase;white-space:nowrap;box-shadow:0 1px 2px rgba(0,0,0,.3)}
  .cta svg{flex:none}
</style>
</head>
<body>
<svg width="0" height="0" style="position:absolute" aria-hidden="true">
  <defs>
    <linearGradient id="greenBand" x1="0" y1="0" x2="1" y2="0">
      <stop offset="0" stop-color="#4f9a0b"/>
      <stop offset="1" stop-color="#9fd21f"/>
    </linearGradient>
  </defs>
</svg>

<main class="sheet">
  <p class="sheet-note sheet-note--top">Images are sized down for preview</p>

  <!-- skyscraper left -->
  <section class="banner" style="left:43px;top:112px;width:269px;height:536px">
    <svg class="wave wave--top" width="269" height="200" viewBox="0 0 100 100" preserveAspectRatio="none" aria-hidden="true">
      <path d="M0 0H100V55C70 70 35 50 0 72Z" fill="url(#greenBand)"/>
      <path d="M0 72C35 50 70 70 100 55V60C70 75 35 55 0 77Z" fill="var(--gold)"/>
    </svg>
    <div class="logo" style="left:79px;top:10px;width:112px;height:112px;font-size:20px">Your<br>FitRoute</div>
    <h2 class="headline" style="left:0;top:138px;width:269px;text-align:center;font-size:22px">Persönlicher Diätplan<br>zum Abnehmen?</h2>
    <div class="product" role="img" aria-label="Ebook-Cover und CD des Diätplans" style="left:12px;top:278px;width:120px;height:160px"></div>
    <div class="photo" role="img" aria-label="Foto einer schlanken Frau mit Maßband" style="left:105px;top:200px;width:150px;height:290px"></div>
    <svg class="wave wave--bottom" width="269" height="80" viewBox="0 0 100 100" preserveAspectRatio="none" aria-hidden="true">
      <path d="M0 30C35 10 70 30 100 15V100H0Z" fill="url(#greenBand)"/>
      <path d="M0 22C35 2 70 22 100 7V15C70 30 35 10 0 30Z" fill="var(--gold)"/>
    </svg>
    <a class="cta" style="left:27px;top:483px;width:215px;height:36px;font-size:15px">Jetzt informieren
      <svg width="18" height="18" viewBox="0 0 20 20" aria-hidden="true"><circle cx="10" cy="10" r="9" fill="#fff" opacity=".9"/><path d="M8 5l5 5-5 5" stroke="#f07800" stroke-width="2.5" fill="none"/></svg></a>
  </section>

  <!-- large leaderboard -->
  <section class="banner" style="left:320px;top:112px;width:683px;height:170px">
    <svg class="wave wave--top" width="683" height="170" viewBox="0 0 100 100" preserveAspectRatio="none" aria-hidden="true">
      <path d="M0 0H22C14 30 18 70 30 100H0Z" fill="url(#greenBand)"/>
      <path d="M22 0H24C16 30 20 70 32 100H30C18 70 14 30 22 0Z" fill="var(--gold)"/>
      <path d="M55 100C70 80 85 92 100 75V100Z" fill="url(#greenBand)"/>
    </svg>
    <div class="logo" style="left:8px;top:28px;width:112px;height:112px;font-size:20px">Your<br>FitRoute</div>
    <h2 class="headline" style="left:140px;top:24px;font-size:25px">Persönlicher<br>Diätplan zum<br>Abnehmen?</h2>
    <a class="cta" style="left:142px;top:123px;width:140px;height:24px;font-size:11px">Jetzt informieren
      <svg width="12" height="12" viewBox="0 0 20 20" aria-hidden="true"><circle cx="10" cy="10" r="9" fill="#fff" opacity=".9"/><path d="M8 5l5 5-5 5" stroke="#f07800" stroke-width="2.5" fill="none"/></svg></a>
    <div class="photo" role="img" aria-label="Foto einer schlanken Frau mit Maßband" style="left:335px;top:4px;width:130px;height:166px"></div>
    <div class="product" role="img" aria-label="Ebook-Cover, CD und Seiten des Diätplans" style="left:480px;top:18px;width:150px;height:140px"></div>
  </section>

  <!-- skyscraper right -->
  <section class="banner" style="left:1014px;top:112px;width:143px;height:534px">
    <svg class="wave wave--top" width="143" height="130" viewBox="0 0 100 100" preserveAspectRatio="none" aria-hidden="true">
      <path d="M0 0H100V58C70 72 35 52 0 70Z" fill="url(#greenBand)"/>
      <path d="M0 70C35 52 70 72 100 58V64C70 78 35 58 0 76Z" fill="var(--gold)"/>
    </svg>
    <div class="logo" style="left:34px;top:6px;width:76px;height:76px;font-size:13px">Your<br>FitRoute</div>
    <h2 class="headline" style="left:8px;top:108px;width:130px;font-size:19px">Persönlicher<br>Diätplan zum<br>Abnehmen?</h2>
    <div class="product" role="img" aria-label="Ebook-Cover und CD des Diätplans" style="left:8px;top:200px;width:118px;height:100px"></div>
    <div class="photo" role="img" aria-label="Foto einer schlanken Frau mit Maßband" style="left:22px;top:300px;width:100px;height:180px"></div>
    <svg class="wave wave--bottom" width="143" height="55" viewBox="0 0 100 100" preserveAspectRatio="none" aria-hidden="true">
      <path d="M0 30C35 10 70 30 100 15V100H0Z" fill="url(#greenBand)"/>
    </svg>
    <a class="cta" style="left:6px;top:495px;width:131px;height:24px;font-size:10px">Jetzt informieren
      <svg width="11" height="11" viewBox="0 0 20 20" aria-hidden="true"><circle cx="10" cy="10" r="9" fill="#fff" opacity=".9"/><path d="M8 5l5 5-5 5" stroke="#f07800" stroke-width="2.5" fill="none"/></svg></a>
  </section>

  <!-- leaderboard -->
  <section class="banner" style="left:320px;top:290px;width:654px;height:79px">
    <svg class="wave wave--top" width="654" height="79" viewBox="0 0 100 100" preserveAspectRatio="none" aria-hidden="true">
      <path d="M0 0H12C9 35 10 70 15 100H0Z" fill="url(#greenBand)"/>
      <path d="M72 100C76 60 74 30 78 0H100V100Z" fill="url(#greenBand)"/>
      <path d="M70 100C74 60 72 30 76 0H78C74 30 76 60 72 100Z" fill="var(--gold)"/>
    </svg>
    <div class="logo" style="left:6px;top:5px;width:68px;height:68px;font-size:12px">Your<br>FitRoute</div>
    <div class="photo" role="img" aria-label="Foto einer schlanken Frau mit Maßband" style="left:100px;top:2px;width:64px;height:77px"></div>
    <h2 class="headline" style="left:215px;top:4px;font-size:18px;text-align:center;line-height:1.15">Persönlicher<br>Diätplan zum<br>Abnehmen?</h2>
    <div class="product" role="img" aria-label="Ebook-Cover und CD des Diätplans" style="left:385px;top:6px;width:78px;height:66px"></div>
    <a class="cta" style="left:485px;top:25px;width:160px;height:28px;font-size:12px">Jetzt informieren
      <svg width="13" height="13" viewBox="0 0 20 20" aria-hidden="true"><circle cx="10" cy="10" r="9" fill="#fff" opacity=".9"/><path d="M8 5l5 5-5 5" stroke="#f07800" stroke-width="2.5" fill="none"/></svg></a>
  </section>

  <!-- small banner wide -->
  <section class="banner" style="left:320px;top:380px;width:421px;height:52px">
    <svg class="wave wave--top" width="421" height="52" viewBox="0 0 100 100" preserveAspectRatio="none" aria-hidden="true">
      <path d="M0 0H13C10 35 11 70 15 100H0Z" fill="url(#greenBand)"/>
      <path d="M72 100C75 60 73 30 76 0H100V100Z" fill="url(#greenBand)"/>
    </svg>
    <div class="logo" style="left:5px;top:3px;width:46px;height:46px;font-size:8px;border-width:2px">Your<br>FitRoute</div>
    <div class="photo" role="img" aria-label="Foto einer schlanken Frau mit Maßband" style="left:70px;top:2px;width:42px;height:50px"></div>
    <h2 class="headline" style="left:130px;top:3px;font-size:12px;text-align:center;line-height:1.13">Persönlicher<br>Diätplan zum<br>Abnehmen?</h2>
    <div class="product" role="img" aria-label="Ebook-Cover und CD des Diätplans" style="left:240px;top:5px;width:56px;height:42px"></div>
    <a class="cta" style="left:310px;top:16px;width:104px;height:20px;font-size:8px">Jetzt informieren
      <svg width="9" height="9" viewBox="0 0 20 20" aria-hidden="true"><circle cx="10" cy="10" r="9" fill="#fff" opacity=".9"/><path d="M8 5l5 5-5 5" stroke="#f07800" stroke-width="2.5" fill="none"/></svg></a>
  </section>

  <!-- small banner short -->
  <section class="banner" style="left:749px;top:380px;width:209px;height:52px">
    <svg class="wave wave--top" width="209" height="52" viewBox="0 0 100 100" preserveAspectRatio="none" aria-hidden="true">
      <path d="M0 0H26C21 35 23 70 30 100H0Z" fill="url(#greenBand)"/>
    </svg>
    <div class="logo" style="left:5px;top:3px;width:46px;height:46px;font-size:8px;border-width:2px">Your<br>FitRoute</div>
    <div class="photo" role="img" aria-label="Foto einer schlanken Frau mit Maßband" style="left:62px;top:2px;width:40px;height:50px"></div>
    <h2 class="headline" style="left:112px;top:3px;width:92px;font-size:12px;text-align:center;line-height:1.13">Persönlicher<br>Diätplan zum<br>Abnehmen?</h2>
  </section>

  <!-- medium rectangle -->
  <section class="banner" style="left:320px;top:442px;width:269px;height:223px">
    <svg class="wave wave--top" width="269" height="223" viewBox="0 0 100 100" preserveAspectRatio="none" aria-hidden="true">
      <path d="M0 0H100V6C60 10 30 4 0 8Z" fill="url(#greenBand)"/>
      <path d="M0 75C40 68 70 78 100 70V100H0Z" fill="url(#greenBand)"/>
      <path d="M0 72C40 65 70 75 100 67V70C70 78 40 68 0 75Z" fill="var(--gold)"/>
    </svg>
    <h2 class="headline" style="left:12px;top:22px;font-size:23px">Persönlicher<br>Diätplan zum<br>Abnehmen?</h2>
    <div class="photo" role="img" aria-label="Foto einer schlanken Frau mit Maßband" style="left:150px;top:10px;width:100px;height:180px"></div>
    <div class="product" role="img" aria-label="Ebook-Cover und CD des Diätplans" style="left:92px;top:110px;width:60px;height:75px"></div>
    <div class="logo" style="left:8px;top:140px;width:74px;height:74px;font-size:13px">Your<br>FitRoute</div>
    <a class="cta" style="left:95px;top:188px;width:160px;height:26px;font-size:11px">Jetzt informieren
      <svg width="12" height="12" viewBox="0 0 20 20" aria-hidden="true"><circle cx="10" cy="10" r="9" fill="#fff" opacity=".9"/><path d="M8 5l5 5-5 5" stroke="#f07800" stroke-width="2.5" fill="none"/></svg></a>
  </section>

  <!-- square -->
  <section class="banner" style="left:599px;top:442px;width:225px;height:223px">
    <svg class="wave wave--top" width="225" height="223" viewBox="0 0 100 100" preserveAspectRatio="none" aria-hidden="true">
      <path d="M0 0H100V6C60 10 30 4 0 8Z" fill="url(#greenBand)"/>
      <path d="M0 75C40 68 70 78 100 70V100H0Z" fill="url(#greenBand)"/>
      <path d="M0 72C40 65 70 75 100 67V70C70 78 40 68 0 75Z" fill="var(--gold)"/>
    </svg>
    <h2 class="headline" style="left:8px;top:22px;font-size:21px">Persönlicher<br>Diätplan zum<br>Abnehmen?</h2>
    <div class="photo" role="img" aria-label="Foto einer schlanken Frau mit Maßband" style="left:130px;top:8px;width:88px;height:180px"></div>
    <div class="product" role="img" aria-label="Ebook-Cover und CD des Diätplans" style="left:70px;top:105px;width:60px;height:75px"></div>
    <div class="logo" style="left:6px;top:148px;width:66px;height:66px;font-size:11px">Your<br>FitRoute</div>
    <a class="cta" style="left:78px;top:188px;width:140px;height:26px;font-size:10px">Jetzt informieren
      <svg width="11" height="11" viewBox="0 0 20 20" aria-hidden="true"><circle cx="10" cy="10" r="9" fill="#fff" opacity=".9"/><path d="M8 5l5 5-5 5" stroke="#f07800" stroke-width="2.5" fill="none"/></svg></a>
  </section>

  <p class="sheet-note sheet-note--bottom">Check the links in the description<br>to see the animations</p>
</main>
</body>
</html>
```